Event Center Website

We need a new website design for an upscale event center in Reno, Nevada. The building hosts everything from weddings to corporate events to funerals and it competitively more expensive. The overall look and feel is consistent with a Lake Tahoe aesthetic. The current site can be viewed at www.themaplehallevents.com. They are looking for a major upgrade. A sample site they like is www.cliffsidelodgestay.com. We have new photography available (some attached). The site should be very visual. A site map is attached as well for direction on what elements the site should include as well as labels for navigation. I am looking for a home page and sample interior page. Any questions, let me know. Thanks.
Updates

I have added some photography of the center itself for use rather than stock photography. Thanks!

Target Market(s)

Brides, professionals, high-income

Industry/Entity Type

Building

Requirements
Must have
• See site map

```html
<!DOCTYPE html>
<html lang="en">
<head>
<meta charset="utf-8">
<title>Maple Hall – Event Center</title>
<link rel="stylesheet" href="https://fonts.googleapis.com/css2?family=Ubuntu:wght@400;500&display=swap">
<style>
  :root {
    --brown-dark: #532f14;
    --brown-panel: rgba(62, 38, 20, 0.62);
    --orange-nav: rgba(212, 116, 26, 0.88);
    --orange-nav-light: rgba(224, 132, 44, 0.86);
    --orange-line: rgba(140, 70, 14, 0.45);
    --orange-footer: #d9711c;
    --text-light: #ffffff;
    --text-dark: #1f1006;
    --social-rim: #e9e9e9;
  }
  * { margin: 0; padding: 0; box-sizing: border-box; }
  html, body { width: 1200px; height: 881px; overflow: hidden; }
  body { font-family: "Ubuntu", sans-serif; position: relative; background: #3b2a1c; }

  .hero {
    position: absolute; left: 0; top: 0; width: 1200px; height: 812px;
    background:
      radial-gradient(ellipse 330px 150px at 640px 100px, rgba(205, 95, 115, 0.85) 0%, rgba(205, 95, 115, 0) 100%),
      radial-gradient(ellipse 260px 120px at 830px 60px, rgba(226, 160, 170, 0.8) 0%, rgba(226, 160, 170, 0) 100%),
      radial-gradient(ellipse 380px 220px at 740px 700px, rgba(218, 204, 188, 0.95) 0%, rgba(218, 204, 188, 0) 100%),
      radial-gradient(ellipse 120px 260px at 490px 700px, rgba(215, 150, 150, 0.8) 0%, rgba(215, 150, 150, 0) 100%),
      radial-gradient(ellipse 120px 260px at 750px 700px, rgba(215, 150, 150, 0.75) 0%, rgba(215, 150, 150, 0) 100%),
      radial-gradient(ellipse 90px 380px at 1090px 380px, rgba(232, 160, 170, 0.95) 0%, rgba(232, 160, 170, 0) 100%),
      radial-gradient(ellipse 260px 200px at 660px 330px, rgba(235, 240, 225, 0.9) 0%, rgba(235, 240, 225, 0) 100%),
      radial-gradient(ellipse 360px 300px at 700px 260px, rgba(140, 175, 90, 0.95) 0%, rgba(140, 175, 90, 0) 100%),
      radial-gradient(ellipse 200px 260px at 990px 300px, rgba(210, 225, 200, 0.9) 0%, rgba(210, 225, 200, 0) 100%),
      radial-gradient(ellipse 80px 300px at 90px 300px, rgba(120, 150, 70, 0.8) 0%, rgba(120, 150, 70, 0) 100%),
      linear-gradient(180deg, rgba(0,0,0,0) 80%, rgba(60, 48, 46, 0.55) 100%),
      linear-gradient(90deg, #5a3a22 0%, #7a5232 6%, #8c6a40 14%, #7c5a34 36%, #a06a3c 40%, #9aa66c 50%, #b8c49a 62%, #c8cdb4 72%, #a06a3c 84%, #d49aa2 90%, #8c5a38 96%, #6b4a2c 100%);
  }

  .sidebar { position: absolute; left: 124px; top: 0; width: 279px; height: 812px; }

  .brand { position: absolute; left: 0; top: 0; width: 279px; height: 182px; }
  .brand svg { position: absolute; left: 0; top: 0; }
  .brand-name {
    position: absolute; left: 41px; top: 45px;
    display: flex; align-items: center; gap: 12px;
    color: var(--text-light); font-size: 30px; font-weight: 400; letter-spacing: 0.5px;
  }
  .brand-mark { width: 68px; height: 64px; background: var(--text-light); flex: none; }

  .main-nav { position: absolute; left: 0; top: 177px; width: 279px; }
  .main-nav a {
    display: flex; align-items: center; justify-content: center;
    height: 51.4px;
    background: linear-gradient(180deg, var(--orange-nav-light), var(--orange-nav));
    border-top: 1px solid var(--orange-line);
    color: var(--text-light); text-decoration: none; font-size: 20.5px; font-weight: 400;
  }
  .main-nav a:first-child { border-top: none; }

  .social {
    position: absolute; left: 0; top: 691px; width: 279px; height: 121px;
    background: var(--brown-panel);
    display: flex; justify-content: center; gap: 22px; padding-top: 29px;
  }
  .social-link {
    width: 55px; height: 55px; border-radius: 50%;
    border: 4px solid var(--social-rim);
    box-shadow: 0 2px 4px rgba(0,0,0,0.45), inset 0 -6px 10px rgba(0,0,0,0.25);
  }
  .social-link.one { background: radial-gradient(circle at 40% 35%, #4c6db0, #2f4b86); }
  .social-link.two { background: radial-gradient(circle at 40% 35%, #48b8ee, #1d8ecf); }
  .social-link.three { background: radial-gradient(circle at 40% 35%, #4aa6dc, #2479b4); }

  .site-footer {
    position: absolute; left: 0; top: 812px; width: 1200px; height: 69px;
    background: var(--orange-footer);
    display: flex; align-items: center; padding-left: 140px;
    color: var(--text-dark); font-size: 20.5px;
  }
</style>
</head>
<body>
  <div class="hero" role="img" aria-label="Photograph of a sweetheart table with rose-textured linens, pink chair sashes and a floral chandelier arrangement in front of large wood-framed windows"></div>

  <aside class="sidebar">
    <div class="brand">
      <svg width="279" height="182" viewBox="0 0 279 182" aria-hidden="true">
        <path d="M0 0 H279 V176 L240 170 L190 158 L150 146 L110 156 L60 168 L0 176 Z" fill="var(--brown-dark)"/>
      </svg>
      <div class="brand-name"><span class="brand-mark"></span>Maple Hall</div>
    </div>

    <nav class="main-nav">
      <a href="#">HOME</a>
      <a href="#">ABOUT US</a>
      <a href="#">GALLERY</a>
      <a href="#">WEDDINGS</a>
      <a href="#">MEETINGS</a>
      <a href="#">OTHER EVENTS</a>
      <a href="#">CATERING</a>
      <a href="#">MENUS</a>
      <a href="#">FAQS</a>
      <a href="#">TESTIMONIALS</a>
    </nav>

    <div class="social">
      <a class="social-link one" href="#" aria-label="Social link 1"></a>
      <a class="social-link two" href="#" aria-label="Social link 2"></a>
      <a class="social-link three" href="#" aria-label="Social link 3"></a>
    </div>
  </aside>

  <footer class="site-footer">©copyrights 2014 Themaplehallevents.com.All rights Reserved</footer>
</body>
</html>
```